Website Redesign for an Appointment Setting and Lead Generation Company.

I need to redesign an existing website. The website that we are looking to be redesigned is www.farlinqo.com. FarLinqo is a B2B appointment setting organization. The idea is to present a modern look website for professional services company. The idea is to engage the user, look at various services and generate more inbound leads for the website

Target Market(s)

US, APAC, Europe, UK. Focused on B2B companies more than $100 Mn

Industry/Entity Type

Professional Service

Number of Pages Required

5+ page

Font styles to use
Other font styles liked:
• Roboto

Requirements
Must have
• Home Page - Banner Image, Section for Client testimonials
Industry Page - To show industry capabilities
Services Page - To show service capabilities
Blogs Page - to show blogs
Offerings Page - Offerings Page
Nice to have
• I would like to have a elegant design with small animation. Preferably use colors from the logo attached. Use infographics where possible

```html
<!DOCTYPE html>
<html lang="en">
<head>
<meta charset="utf-8">
<title>Sales Cadence Elements That Can Turn Your Sales Game | FarLinqo</title>
<link rel="stylesheet" href="https://fonts.googleapis.com/css2?family=Noto+Sans:ital,wght@0,400;0,500;0,700;1,400;1,700&family=Roboto:wght@300;400;500;700&display=swap">
<style>
:root{
  --brand-red:#c0272d;
  --ink:#2b2b2b;
  --body:#3a3a3a;
  --muted:#8a8a8a;
  --line:#d6d6d6;
  --panel:#f4f4f4;
  --band:#f5f5f5;
  --button:#c4c4c4;
  --dark:#333333;
  --white:#ffffff;
}
*{box-sizing:border-box;margin:0;padding:0}
html,body{width:1200px;height:3922px;overflow:hidden}
body{position:relative;background:var(--white);font-family:"Roboto",Arial,sans-serif;color:var(--body)}
.abs{position:absolute}
.serif-free{font-family:"Noto Sans",Verdana,sans-serif}

/* header */
.brand{display:flex;align-items:center;gap:8px}
.brand-mark{width:22px;height:22px;background:var(--brand-red)}
.brand-name{font-size:27px;font-weight:500;color:var(--brand-red);letter-spacing:-.3px;line-height:1}
.nav{top:26px;left:465px;font-size:14px;color:#777}
.nav a{position:absolute;white-space:nowrap;color:#777;text-decoration:none}
.nav a.active{color:var(--brand-red)}
.nav .caret{font-size:9px;margin-left:4px;color:#aaa}

/* hero */
.hero{left:126px;top:91px;width:658px;height:308px;
  background:linear-gradient(90deg,#d9d2a8 0%,#e7e6e2 22%,#eeeeec 60%,#e4e5e3 100%)}
.meta{left:126px;top:428px;width:660px;font-size:12px;color:var(--muted);letter-spacing:1px}
.meta .share{position:absolute;left:282px;top:-6px;display:flex;gap:14px}
.meta .share span{width:22px;height:22px;background:var(--ink);display:block}
.meta .date{position:absolute;right:0;top:0}
.post-title{left:126px;top:466px;font-size:19px;font-weight:400;color:var(--ink);letter-spacing:1.1px;white-space:nowrap}

/* article */
.article{left:126px;top:546px;width:660px;font-size:13px;line-height:22.8px;letter-spacing:.75px;color:var(--body)}
.article p{margin-bottom:22.8px}
.article h2{font-size:16px;font-weight:500;color:var(--ink);letter-spacing:1.1px;margin:-2px 0 16px}
.article em{font-weight:700}
.post-btn{top:2470px;width:186px;height:51px;background:var(--button);color:var(--white);font-size:12.5px;display:flex;align-items:center;justify-content:center;letter-spacing:.2px}

/* sidebar */
.sidebar{left:868px;top:91px;width:271px;height:1130px;background:var(--panel)}
.search{left:26px;top:46px;width:219px;height:46px;border:3px solid #dedede;background:var(--white);font-size:12px;color:#b3b3b3;padding:12px 20px}
.side-h{left:28px;font-size:13px;color:#444}
.side-rule{left:28px;width:217px;height:1px;background:var(--line)}
.side-social{left:28px;top:210px;display:flex;gap:18px}
.side-social span{width:14px;height:14px;border-radius:50%;background:#d8d8d8;display:block}
.side-post{left:29px;display:flex;gap:11px;width:220px}
.thumb{width:67px;height:67px;flex:none}
.side-post p{font-size:11.5px;line-height:15.5px;color:#444;letter-spacing:.4px}
.float-social{left:1146px;top:462px;display:flex;flex-direction:column;gap:22px}
.float-social span{width:22px;height:18px;border-radius:4px;background:#ececec;display:block}

/* contact */
.band{left:0;top:2761px;width:1200px;height:553px;background:var(--band)}
.contact{left:327px;top:2655px;width:546px;height:766px;background:var(--white);box-shadow:0 2px 10px rgba(0,0,0,.08)}
.contact h3{position:absolute;top:32px;width:100%;text-align:center;font-size:19px;font-weight:400;color:#555;letter-spacing:.5px}
.field{position:absolute;height:22px;border-bottom:1px solid #bdbdbd;font-size:11px;color:#aaa}
.field .req{position:absolute;right:0;top:4px;color:var(--brand-red)}
.contact .note{position:absolute;left:75px;font-size:11.5px;line-height:23px;color:#555}
.contact .note a{color:var(--brand-red);text-decoration:none}
.check{position:absolute;left:75px;top:363px;width:10px;height:10px;border:1px solid #777}
.submit{position:absolute;left:75px;top:670px;width:127px;height:40px;background:var(--dark);color:var(--white);font-size:13px;display:flex;align-items:center;justify-content:center;box-shadow:0 3px 6px rgba(0,0,0,.25)}

/* footer */
.foot-h{top:3474px;font-size:15.5px;font-weight:500;color:var(--brand-red);padding-bottom:6px;border-bottom:3px solid var(--brand-red)}
.foot-list{top:3517px;list-style:none;font-size:14px;color:#555}
.foot-list li{height:39.6px}
.foot-social{left:155px;top:3624px;display:flex;gap:47px}
.foot-social span{width:20px;height:20px;border:1.5px solid #888;border-radius:50%;display:block}
.to-top{left:1112px;top:3778px;width:40px;height:40px;border-radius:50%;background:var(--white);box-shadow:0 1px 6px rgba(0,0,0,.18)}
.copyright{left:0;top:3853px;width:1200px;height:69px;background:#e6e6e6;display:flex;align-items:center;justify-content:center;font-size:11.5px;font-weight:500;color:#333}
.copyright .sep{width:2px;height:20px;background:var(--brand-red);margin:0 18px}
.copyright a{color:var(--brand-red);text-decoration:none}
</style>
</head>
<body>

<header>
  <div class="abs brand" style="left:126px;top:16px"><span class="brand-mark"></span><span class="brand-name">FarLinqo</span></div>
  <nav class="abs nav">
    <a style="left:0">Home</a>
    <a style="left:66px">About<span class="caret">&#8964;</span></a>
    <a style="left:134px">Services<span class="caret">&#8964;</span></a>
    <a style="left:216px">Our Expertise<span class="caret">&#8964;</span></a>
    <a class="active" style="left:330px">Library<span class="caret">&#8964;</span></a>
    <a style="left:403px">Contact Us<span class="caret">&#8964;</span></a>
  </nav>
  <svg class="abs" style="left:1060px;top:24px" width="20" height="20" viewBox="0 0 20 20" fill="none" stroke="#333" stroke-width="1.8"><circle cx="8.5" cy="8.5" r="6.5"/><path d="M13.5 13.5 18 18"/></svg>
</header>

<div class="abs hero" role="img" aria-label="Hand holding a yellow funnel with banknotes passing through it"></div>

<div class="abs meta serif-free">5 mins read
  <div class="share"><span></span><span></span><span></span></div>
  <span class="date">10,May,2020</span>
</div>
<h1 class="abs post-title serif-free">Sales Cadence Elements That Can Turn Your Sales Game</h1>

<article class="abs article serif-free">
  <p>No matter what business you own, crafting a well-thought sales cadence is a crucial part of survival. Now many businesses invest in high-rolling sales teams and the latest technology. But, there’s a major distinction between having the right tools at your disposal and utilizing them successfully. A well-crafted sales cadence put into action strategically not only helps run a seamless sales process but goes for winning sales and adding more brand credibility.</p>
  <p>Cadences permit sales professionals to follow explicit, top-performing sales playbooks to ensure they are proficient and viable in conducting their sales journey. Deploying winning sales cadences can positively impact the functioning of a business, however, you need completely understand the dynamics of a good sales cadence and implement them entirely.</p>
  <p>You do not need to be a data scientist to comprehend the elements within a sales cadence, but you do need to know your data well. Do take note of the sales engagement platform you use and the data you retrieve. A half-baked sales cadence run on your gut instincts and unreliable sales data would reap half-baked sales efforts, accompanied by loss of time and money. If you wish to put on an A-game, you constantly need to improvise your cadence and understand all the elements to better optimize them and gain a worthier outcome.</p>
  <p>5 notable elements can bring about a massive improvement in your sales cadence. If done right, they have the potential to directly impacting your success. Let us have a look:</p>
  <h2>Counting The Steps Involved</h2>
  <p>You must know the number of steps that you want your cadence to possess. Steps are a single action a sales profession is required to take within the entire cadence. Ideally, as a popular practice, the best sales cadences usually have five to twelve steps. However, if you do believe your sales cycle is particularly short, choose between five to eight steps.</p>
  <h2>Identifying The Step Channel</h2>
  <p>Now that you have the number of steps involved, you do need to identify the medium you would initiate your outreach with. Within a successful cadence, your channel preferences can be <em><i>Email, Phone Call + Voicemail,</i></em> and <em><i>ProNetwork</i></em>. Incorporating and leveraging these three mediums in your sales strategy can help engage better with a potential lead and also give sales professionals better visibility to be noticed. Besides, merging videos and direct mail to the channel medium can convert this effort into a “five-touch points” to improve interaction and drive response rates.</p>
  <h2>Deciding Upon The Cadence Length</h2>
  <p>Do not confuse this action with the number of steps within the sales cadence. The length of a sales cadence signifies the number of days involved between the steps to conduct the entire process. Ideally deciding upon the length of a cadence is the only area where it has less relevance on the outcome and requires a more hit and try approach. The pace of the sales cadence in the form of its length is something you can decipher depending on the response you receive from the prospects. If you consider your target audience to be busy executives with less attention span, you might consider a day gap between the steps. However, if you gauge that it appears to be too reckless an action, you can stretch the length of days between the steps.</p>
  <h2>Calculating The Right Step Timing</h2>
  <p>As they say, <em><i>timing is everything!</i></em> Within a sales cadence, sales professionals need to maintain great timing to ensure they are not overwhelming a prospect with their engagement efforts. Often called a ‘sales touch’, it needs to be timed in such a fashion that it looks natural to the prospect. You do not need to bombard the potential lead with email, phone call, voicemail, and ProNetwork messages on day 1. The sales touch needs to be subtle, yet impactful. A perfect sales cadence would time the first call and first email on day one and give it a day’s rest for the upcoming engagement activities.</p>
  <h2>Working on a Cadence Type</h2>
  <p>Now a cadence type differs from one type of sales strategy to the next you may jump to. However, the core idea of it remains the same: it needs to be consistent and requires progressive touches to bring your presence and purpose known to the prospect. Your cadence type could be communicated to the sales professionals depending on the sales journey you wish to take. You can create a cadence type that is slow and steady, it is bound to involve a long nurturing sales cycle. On the contrary, a fast-paced approach might include a more aggressive cadence type that is fierce and quick.</p>
  <p>A sales cadence helps your sales team travel and skillfully sail through the ever-so challenging waters of revenue generation and lead nurturing. You must understand that sales cadences not only bring systematic action on the table but also help drive more momentum within a sales team as they can deliver better and show consistent performance. A well-thought sales cadence is a positive step for growing a business and strengthening your team into specialized sales professionals.</p>
</article>

<div class="abs post-btn" style="left:126px">PREVIOUS POST</div>
<div class="abs post-btn" style="left:600px">NEXT POST</div>

<aside class="abs sidebar">
  <div class="abs search">Search</div>
  <div class="abs side-h" style="top:153px">Follow Us</div>
  <div class="abs side-rule" style="top:180px"></div>
  <div class="abs side-social"><span></span><span></span><span></span></div>
  <div class="abs side-h" style="top:313px">Latest Posts</div>
  <div class="abs side-rule" style="top:340px"></div>
  <div class="abs side-post serif-free" style="top:366px"><div class="thumb" role="img" aria-label="Wooden blocks on a table" style="background:linear-gradient(135deg,#c9a47a,#efe7dc)"></div><p>Taking The Right Sales Approach: Outbound or Inbound ?</p></div>
  <div class="abs side-post serif-free" style="top:454px"><div class="thumb" role="img" aria-label="Dark blue blog cover graphic" style="background:linear-gradient(135deg,#2d3a4c,#6a7787)"></div><p>Taking The Right Sales Approach: Outbound or Inbound ?</p></div>
  <div class="abs side-post serif-free" style="top:543px"><div class="thumb" role="img" aria-label="Football match scene in a stadium" style="background:linear-gradient(135deg,#1f3350,#4d6a8a)"></div><p>Taking The Right Sales Approach: Outbound or Inbound ?</p></div>
  <div class="abs side-h" style="top:668px">Next Posts</div>
  <div class="abs side-rule" style="top:695px"></div>
  <div class="abs side-post serif-free" style="top:722px"><div class="thumb" role="img" aria-label="Wooden blocks on a table" style="background:linear-gradient(135deg,#c9a47a,#efe7dc)"></div><p>Taking The Right Sales Approach: Outbound or Inbound ?</p></div>
  <div class="abs side-post serif-free" style="top:811px"><div class="thumb" role="img" aria-label="Bright yellow abstract graphic" style="background:radial-gradient(circle at 40% 40%,#fff6c4,#f2c21a)"></div><p>Achieving Sales Target Through The Referral Road</p></div>
  <div class="abs side-post serif-free" style="top:899px"><div class="thumb" role="img" aria-label="Dark blue blog cover graphic" style="background:linear-gradient(135deg,#2d3a4c,#6a7787)"></div><p>Reigniting Sales: 5 Ways To Warm Up Cold Leads</p></div>
</aside>

<div class="abs float-social"><span></span><span></span><span></span><span></span></div>

<div class="abs band"></div>
<section class="abs contact">
  <h3>Contact Us</h3>
  <div class="field" style="left:75px;top:111px;width:165px">First name<span class="req">*</span></div>
  <div class="field" style="left:304px;top:111px;width:164px">Email<span class="req">*</span></div>
  <div class="field" style="left:75px;top:158px;width:165px">Last name<span class="req">*</span></div>
  <div class="field" style="left:304px;top:158px;width:164px">Phone number<span class="req">*</span></div>
  <div class="field" style="left:75px;top:206px;width:192px">Company name<span class="req" style="right:-6px">*</span></div>
  <div class="field" style="left:75px;top:313px;width:392px">Message</div>
  <span class="check"></span>
  <p class="note" style="left:102px;top:355px">I agree to receive other communications<br>from FarLinqo.</p>
  <p class="note" style="top:417px;width:410px">You can unsubscribe from these communications at anytime. For more information on how to unsubscribe, our privacy practices, and how we are committed to protecting and respecting your privacy, please review our <a>Privacy Policy</a>.</p>
  <p class="note" style="top:531px;width:240px">By clicking submit below, you consent to allow FarLinqo to store and process the personal information submitted above to provide you the content requested.</p>
  <div class="submit">Submit</div>
</section>

<footer>
  <div class="abs brand" style="left:154px;top:3478px"><span class="brand-mark"></span><span class="brand-name">FarLinqo</span></div>
  <div class="abs foot-social"><span></span><span></span><span></span></div>
  <div class="abs foot-h" style="left:493px">ABOUT US</div>
  <ul class="abs foot-list" style="left:493px"><li>About</li><li>Our Team</li><li>Awards</li><li>Our Partnerships</li><li>Our Differentiators</li><li>Locations</li></ul>
  <div class="abs foot-h" style="left:693px">SERVICES</div>
  <ul class="abs foot-list" style="left:693px"><li>B2B Appointment Setting</li><li>Account Based Marketing</li><li>Research As A Service</li><li>Event Audience Acquisition</li><li>Staffing &amp; Talent Acquisition</li><li>Digital Marketing</li><li>Social Media Research</li><li>Lead Nurturing</li></ul>
  <div class="abs foot-h" style="left:960px">LIBRARY</div>
  <ul class="abs foot-list" style="left:960px"><li>Videos</li><li>Infographics</li><li>Blog</li><li>Case Studies</li></ul>
  <div class="abs to-top"><svg width="40" height="40" viewBox="0 0 40 40" fill="none" stroke="var(--brand-red)" stroke-width="1.4"><path d="M15 22l5-5 5 5"/></svg></div>
  <div class="abs copyright">Copyright All Rights Reserved © 2020.<span class="sep"></span><a>Privacy Policy</a></div>
</footer>

</body>
</html>
```